Business card for law firm

Need business card for new law firm. Think confident, authoritative, conservative, but not stuffy or old-fashioned.

Contact Information for Business Card

Content for card - logo (uploaded), plus the following:

Paul Whitcombe (larger font)
Managing Partner (larger font, but not as large as name)
Level 9, 7 Ferris Lane
Sydney NSW 2000
Main Tel 02 9364 2710
Direct Tel 02 8472 3159
Email paul@qvlegal.com.au
www.qvlegal.com.au

Letterhead design should include logo plus:
Level 9, 7 Ferris Lane
Sydney NSW 2000
Tel 02 8472 3159
www.qvlegal.com.au

```html
<!DOCTYPE html>
<html lang="en">
<head>
<meta charset="utf-8">
<title>Quayvale Legal – Business Card</title>
<link href="https://fonts.googleapis.com/css2?family=Open+Sans:wght@400;700&display=swap" rel="stylesheet">
<style>
  :root {
    --page-bg: #e9e9ec;
    --navy: #0c1f5c;
    --white: #ffffff;
    --black: #0b0b0c;
    --ink: #222226;
    --muted: #55565c;
    --rule: #c9c9cf;
  }
  * { box-sizing: border-box; margin: 0; padding: 0; }
  html, body {
    width: 1200px; height: 960px; overflow: hidden;
    background: var(--page-bg);
    font-family: "Open Sans", Arial, sans-serif;
  }
  .sheet {
    width: 1200px; height: 960px;
    display: flex; flex-direction: column; align-items: center; justify-content: center;
    gap: 40px;
  }
  .card {
    position: relative;
    width: 760px; height: 420px;
    overflow: hidden;
    box-shadow: 0 6px 18px rgba(0,0,0,.18);
  }
  /* Back */
  .card-back { background: var(--black); color: var(--white); }
  .back-brand {
    position: absolute; left: 0; right: 0; top: 120px;
    display: flex; flex-direction: column; align-items: center; gap: 22px;
  }
  .brand-square { width: 90px; height: 90px; background: var(--white); }
  .back-name { font-size: 30px; font-weight: 400; letter-spacing: 4px; text-transform: uppercase; }
  .back-web {
    position: absolute; left: 0; right: 0; bottom: 56px;
    text-align: center; font-size: 16px; letter-spacing: 4px;
  }
  /* Front */
  .card-front { background: var(--navy); }
  .front-shape { position: absolute; inset: 0; }
  .front-brand {
    position: absolute; left: 60px; width: 290px; top: 118px;
    display: flex; flex-direction: column; align-items: center; gap: 22px;
  }
  .front-brand .brand-square { width: 56px; height: 56px; background: var(--navy); }
  .front-name {
    font-size: 30px; font-weight: 400; color: var(--ink);
    letter-spacing: 3px; text-transform: uppercase; white-space: nowrap;
  }
  .divider {
    position: absolute; left: 366px; top: 140px; width: 1px; height: 190px;
    background: var(--rule);
  }
  .contact { position: absolute; left: 388px; top: 142px; color: var(--ink); }
  .contact-name { font-size: 23px; font-weight: 700; color: var(--navy); text-transform: uppercase; line-height: 1.1; }
  .contact-title { font-size: 16px; color: var(--muted); text-transform: uppercase; margin-top: 2px; }
  .contact-address { font-size: 17px; line-height: 1.4; margin-top: 12px; }
  .contact-lines { list-style: none; margin-top: 10px; font-size: 17px; line-height: 1.45; }
  .contact-lines li { display: flex; align-items: center; gap: 8px; }
  .contact-lines svg { width: 15px; height: 15px; flex: none; }
</style>
</head>
<body>
<main class="sheet">

  <section class="card card-back" aria-label="Card back">
    <div class="back-brand">
      <div class="brand-square"></div>
      <div class="back-name">Quayvale Legal</div>
    </div>
    <div class="back-web">www.qvlegal.com.au</div>
  </section>

  <section class="card card-front" aria-label="Card front">
    <svg class="front-shape" viewBox="0 0 760 420" width="760" height="420" aria-hidden="true">
      <ellipse cx="380" cy="210" rx="345" ry="310" fill="#ffffff"/>
    </svg>

    <div class="front-brand">
      <div class="brand-square"></div>
      <div class="front-name">Quayvale Legal</div>
    </div>

    <div class="divider"></div>

    <div class="contact">
      <p class="contact-name">Paul Whitcombe</p>
      <p class="contact-title">Managing Partner</p>
      <p class="contact-address">Level 9, 7 Ferris Lane<br>Sydney NSW 2000</p>
      <ul class="contact-lines">
        <li>
          <svg viewBox="0 0 16 16"><circle cx="8" cy="8" r="8" fill="#0c1f5c"/><path d="M5 4.5c.6-.4 1.2 0 1.4.6l.3 1c.1.4-.1.7-.4.9.4.9 1.1 1.6 2 2 .2-.3.5-.5.9-.4l1 .3c.6.2 1 .8.6 1.4-.5.8-1.4 1-2.3.6-2-.9-3.5-2.4-4.4-4.4-.3-.8-.1-1.6.9-2z" fill="#fff"/></svg>
          <span>02 9364 2710(Main)</span>
        </li>
        <li>
          <svg viewBox="0 0 16 16"><circle cx="8" cy="8" r="8" fill="#0c1f5c"/><path d="M5 4.5c.6-.4 1.2 0 1.4.6l.3 1c.1.4-.1.7-.4.9.4.9 1.1 1.6 2 2 .2-.3.5-.5.9-.4l1 .3c.6.2 1 .8.6 1.4-.5.8-1.4 1-2.3.6-2-.9-3.5-2.4-4.4-4.4-.3-.8-.1-1.6.9-2z" fill="#fff"/></svg>
          <span>02 8472 3159(Direct)</span>
        </li>
        <li>
          <svg viewBox="0 0 16 16"><circle cx="8" cy="8" r="8" fill="#0c1f5c"/><rect x="4" y="5" width="8" height="6" fill="#fff"/><path d="M4 5l4 3.2L12 5" fill="none" stroke="#0c1f5c" stroke-width="1"/></svg>
          <span>paul@qvlegal.com.au</span>
        </li>
        <li>
          <svg viewBox="0 0 16 16"><circle cx="8" cy="8" r="8" fill="#0c1f5c"/><circle cx="8" cy="8" r="4.5" fill="none" stroke="#fff" stroke-width="1"/><path d="M3.5 8h9M8 3.5c-2 2.5-2 6.5 0 9M8 3.5c2 2.5 2 6.5 0 9" fill="none" stroke="#fff" stroke-width="1"/></svg>
          <span>www.qvlegal.com.au</span>
        </li>
      </ul>
    </div>
  </section>

</main>
</body>
</html>
```